Dov's Personal Training -> also needs a logo

Services Frankston, Mornington, and Somerville

Specializes in in-home personal training

VaultPace style workouts

Not really preferential colors but needs to look modern and not stock photo

Industry/Entity Type

Training

Requirements
Must have
• 30% off first time customers on a package of 10

```html
<!DOCTYPE html>
<html lang="en">
<head>
<meta charset="utf-8">
<title>Dov's Personal Training</title>
<link rel="stylesheet" href="https://fonts.googleapis.com/css2?family=Jost:wght@300;400;600;700&family=Arimo:wght@700&family=Archivo+Black&display=swap">
<style>
  :root {
    --sky: #2a8ff0;
    --deep: #1565c8;
    --glow: #bff4f4;
    --aqua: #52c6d8;
    --teal-dark: #0d3f55;
    --mint: #8ee0c8;
    --white: #ffffff;
    --offer-disc: #c6d6e4;
    --offer-blue: #3d9ff0;
  }
  * { margin: 0; padding: 0; box-sizing: border-box; }
  html, body { width: 1200px; height: 900px; overflow: hidden; }
  body { background: var(--teal-dark); }

  .flyer {
    position: relative;
    width: 1200px;
    height: 900px;
    overflow: hidden;
    font-family: "Jost", sans-serif;
    color: var(--white);
  }

  .backdrop {
    position: absolute;
    inset: 0;
    background:
      linear-gradient(160deg, transparent 38%, rgba(191,244,244,0.55) 50%, transparent 60%),
      linear-gradient(180deg, var(--deep) 0%, var(--sky) 28%, var(--aqua) 52%, #2a7f96 72%, var(--teal-dark) 100%);
  }

  .brand {
    position: absolute;
    left: 52px;
    top: 52px;
    display: flex;
    align-items: center;
    gap: 44px;
  }
  .brand-dot {
    width: 172px;
    height: 172px;
    border-radius: 50%;
    background: var(--mint);
    flex: none;
  }
  .brand-name {
    font-weight: 600;
    color: var(--white);
    line-height: 1;
  }
  .brand-name .main { display: block; font-size: 104px; letter-spacing: 1px; }
  .brand-name .sub { display: block; font-size: 31px; margin-top: 8px; letter-spacing: 0.5px; }

  .details {
    position: absolute;
    left: 54px;
    top: 564px;
    text-transform: uppercase;
  }
  .details h2 {
    font-weight: 700;
    font-size: 34px;
    line-height: 1;
    letter-spacing: -0.5px;
  }
  .area-list { list-style: none; margin-top: 6px; }
  .area-list li {
    font-weight: 400;
    font-size: 31px;
    line-height: 1.1;
    letter-spacing: 0.5px;
  }
  .specialties { margin-top: 22px; }
  .specialty-list { list-style: none; margin-top: 4px; }
  .specialty-list li {
    font-weight: 300;
    font-size: 39px;
    line-height: 1.12;
    letter-spacing: 0.5px;
  }

  .offer-disc {
    position: absolute;
    left: 712px;
    top: 562px;
    width: 580px;
    height: 580px;
    border-radius: 50%;
    background: var(--offer-disc);
    opacity: 0.96;
  }
  .offer {
    position: absolute;
    left: 766px;
    top: 690px;
    color: var(--offer-blue);
  }
  .offer-headline {
    font-family: "Archivo Black", sans-serif;
    font-size: 80px;
    line-height: 0.95;
    letter-spacing: -1px;
  }
  .offer-terms {
    font-family: "Arimo", sans-serif;
    font-weight: 700;
    font-size: 34px;
    line-height: 1.06;
    letter-spacing: -0.3px;
  }
</style>
</head>
<body>
  <main class="flyer">
    <div class="backdrop" role="img" aria-label="Flowing abstract light waves in blue and aqua"></div>

    <header class="brand">
      <span class="brand-dot"></span>
      <div class="brand-name">
        <span class="main">DOVS</span>
        <span class="sub">PERSONAL TRAINING</span>
      </div>
    </header>

    <section class="details">
      <div class="service-areas">
        <h2>Services:</h2>
        <ul class="area-list">
          <li>Frankston</li>
          <li>Mornington</li>
          <li>Somerville</li>
        </ul>
      </div>
      <div class="specialties">
        <h2>Specializes in:</h2>
        <ul class="specialty-list">
          <li>In-home personal training</li>
          <li>VaultPace style workouts</li>
        </ul>
      </div>
    </section>

    <div class="offer-disc"></div>
    <section class="offer">
      <p class="offer-headline">30%OFF</p>
      <p class="offer-terms">first time customers<br>on a package of 10</p>
    </section>
  </main>
</body>
</html>
```